Website for Torvel Capital - investment banking firm

We have a corporate identity (thanks to Ravinka/31842) and want to extend that into a website design.  See the attached zipped files.
We have software folks in-house to do the coding.
See the attached Project Brief & Notes for more details.  Don't worry about the actual text - lorem ipsum will be fine.
The server will be Apache.
Thank you!
Desmond

Industry/Entity Type
Investment

```html
<!DOCTYPE html>
<html lang="en">
<head>
<meta charset="utf-8">
<title>Torvel Capital</title>
<link href="https://fonts.googleapis.com/css2?family=Lato:ital,wght@0,400;0,700;1,400&family=Tinos&family=Mulish:wght@500;600&display=swap" rel="stylesheet">
<style>
:root{
  --brand:#1f4d8f;
  --brand-dark:#173f78;
  --ink:#111;
  --rule:#9fb4cf;
  --white:#fff;
  --sky-top:#8fbbe6;
  --sky-mid:#5a97d8;
  --sky-low:#c9dcef;
}
*{box-sizing:border-box;margin:0;padding:0}
html,body{width:1200px;height:971px;overflow:hidden}
body{position:relative;font-family:"Lato",sans-serif;color:var(--ink);background:#fff}
.abs{position:absolute}

.site-header{left:0;top:0;width:1200px;height:94px;background:linear-gradient(90deg,#fff 0%,#f4f8fc 60%,#e4eef8 100%)}
.brand{left:132px;top:13px;height:66px;display:flex;align-items:center;gap:12px}
.brand-mark{width:52px;height:52px;background:var(--brand)}
.brand-name{font-family:"Tinos",serif;font-size:34px;color:var(--brand);letter-spacing:.5px}
.contact-top{top:10px;display:flex;align-items:center;gap:6px;color:var(--brand)}
.contact-top.email{left:719px;font-size:12.5px;font-weight:700}
.contact-top.phone{left:901px;font-size:19px;font-weight:700;letter-spacing:.5px}
.main-nav{left:498px;top:57px;height:26px;display:flex;align-items:center;font-size:14px;color:#222}
.main-nav a{color:inherit;text-decoration:none;padding:0 13px;line-height:18px;border-left:1px solid var(--rule)}
.main-nav a.no-rule{border-left:none}
.main-nav a.active{background:var(--brand);color:#fff;line-height:26px;padding:0 16px;border:none}

.hero{left:0;top:94px;width:1200px;height:732px;background:linear-gradient(180deg,var(--sky-top) 0%,var(--sky-mid) 50%,var(--sky-low) 85%,#dcdad5 100%)}
.lower-band{left:0;top:568px;width:1200px;height:258px;background:rgba(240,240,238,.55)}

.hero-panel{left:606px;top:218px;width:463px;height:187px;background:rgba(235,242,250,.8);border-radius:3px}
.hero-title{left:26px;top:6px;font-family:"Tinos",serif;font-weight:400;font-size:34px;color:var(--brand)}
.hero-sub{left:26px;top:54px;font-family:"Mulish",sans-serif;font-weight:500;font-size:15.5px;color:#111}
.hero-caps{left:26px;top:84px;font-family:"Mulish",sans-serif;font-weight:600;font-size:17px;color:#111;letter-spacing:.3px}
.cta{left:27px;top:122px}

.card{top:527px;width:288px;height:172px;background:linear-gradient(180deg,rgba(255,255,255,.9) 0,rgba(255,255,255,.55) 40px,rgba(255,255,255,0) 100%);border-radius:5px 5px 0 0}
.card-title{left:14px;top:6px;display:flex;align-items:center;gap:12px;font-family:"Tinos",serif;font-weight:400;font-size:24px}
.card-title .mark{width:28px;height:28px;background:var(--brand)}
.card-title em{font-style:normal;color:var(--brand)}
.card-icon{left:16px;top:53px;width:58px;height:58px;border:2px solid #222;border-radius:50%;display:flex;align-items:center;justify-content:center}
.card-body{left:89px;top:56px;width:194px;height:80px;overflow:hidden;font-size:13px;line-height:20px;color:#222}
.card-body.spaced{letter-spacing:.35px}
.card-body strong{font-weight:700}
.services{list-style:none;height:auto}
.services li{position:relative;padding-left:13px;line-height:16px;margin-bottom:7px}
.services li::before{content:"";position:absolute;left:1px;top:4px;border-left:5px solid #888;border-top:4px solid transparent;border-bottom:4px solid transparent}
.read-more{left:89px;top:145px;font-size:11px;font-weight:700;color:var(--brand);letter-spacing:.2px}

.divider{left:170px;top:705px;width:900px;height:1px;background:linear-gradient(90deg,rgba(150,150,150,0),rgba(150,150,150,.6) 20%,rgba(150,150,150,.6) 80%,rgba(150,150,150,0))}
.testi-label{left:120px;top:729px;width:148px;text-align:right;font-family:"Tinos",serif;font-weight:400;font-size:24px;line-height:30px}
.testi-label em{font-style:normal;color:var(--brand)}
.testi-arrow{left:284px;top:716px}
.testi-quote{left:339px;top:734px;width:710px;font-style:italic;font-size:14px;line-height:20px;color:#222}
.testi-name{left:339px;top:781px;font-style:italic;font-size:14px;color:var(--brand)}

.site-footer{left:0;top:826px;width:1200px;height:145px;background:var(--brand);color:#fff}
.foot-h{font-size:17px;font-weight:700}
.foot-rule{height:1px;background:rgba(255,255,255,.35)}
.address{left:156px;top:56px;font-size:12.5px;line-height:20px}
.foot-line{font-size:13.5px;font-weight:700;display:flex;align-items:center;gap:12px}
.news-input{left:555px;top:60px;width:206px;height:28px;background:var(--brand-dark);border:1px solid #2b5ea3;font-style:italic;font-size:12px;color:#b9c7dc;padding:6px 10px}
.news-go{left:761px;top:60px;width:38px;height:28px;background:#fff;color:var(--brand);font-weight:700;font-size:15px;text-align:center;line-height:28px}
.follow{left:554px;top:103px;display:flex;align-items:center;gap:9px;font-size:15px;font-weight:700}
.social{width:29px;height:29px;border:1.5px solid #fff;border-radius:50%}
.foot-badge{left:917px;top:-25px;width:107px;height:82px;background:#fff;border-radius:0 0 54px 54px;display:flex;align-items:center;justify-content:center}
.foot-badge span{width:48px;height:48px;border-radius:50%;background:var(--brand)}
.copyright{left:864px;top:81px;width:220px;text-align:center;font-size:13px;line-height:20px}
</style>
</head>
<body>

<header class="site-header abs">
  <div class="brand abs">
    <span class="brand-mark"></span>
    <span class="brand-name">Torvel Capital</span>
  </div>
  <div class="contact-top email abs">
    <svg width="32" height="24" viewBox="0 0 32 24"><rect x="1" y="1" width="24" height="22" rx="3" fill="none" stroke="#555" stroke-width="1.5"/><path d="M25 9l5 3-5 3" fill="none" stroke="#555" stroke-width="1.5"/><rect x="6" y="7" width="14" height="10" fill="#333"/><path d="M6 7l7 6 7-6" stroke="#fff" fill="none"/></svg>
    info@torvelcapital.com
  </div>
  <div class="contact-top phone abs">
    <svg width="32" height="24" viewBox="0 0 32 24"><rect x="1" y="1" width="24" height="22" rx="3" fill="none" stroke="#555" stroke-width="1.5"/><path d="M25 9l5 3-5 3" fill="none" stroke="#555" stroke-width="1.5"/><rect x="9" y="5" width="8" height="14" rx="1" fill="#333"/><rect x="10.5" y="7" width="5" height="4" fill="#fff"/></svg>
    469-555-0187
  </div>
  <nav class="main-nav abs">
    <a class="active" href="#">About</a>
    <a class="no-rule" href="#">Services</a>
    <a href="#">Current Engagements</a>
    <a href="#">Completed Transactions</a>
    <a href="#">Contact Us</a>
  </nav>
</header>

<div class="hero abs" role="img" aria-label="Photograph of a man standing on a rock against a sunlit blue sky with clouds"></div>
<div class="lower-band abs"></div>

<section class="hero-panel abs">
  <h1 class="hero-title abs">Private Investment Banking</h1>
  <p class="hero-sub abs">advisory firm that acts as an intermediary on behalf of</p>
  <p class="hero-caps abs">BUYERS &amp; SELLERS OF PRIVATE COMPANIES.</p>
  <svg class="cta abs" width="180" height="48" viewBox="0 0 180 48">
    <path d="M0 0H160L180 24L160 48H0Z" fill="#1f4d8f"/>
    <text x="17" y="31" font-family="Mulish,sans-serif" font-size="18" fill="#fff">Get Started Now</text>
  </svg>
</section>

<section class="card abs" style="left:134px">
  <h2 class="card-title abs"><span class="mark"></span><span><em>Who</em> We Are</span></h2>
  <div class="card-icon abs"><svg width="26" height="26" viewBox="0 0 26 26"><circle cx="13" cy="8" r="6" fill="#222"/><path d="M2 25c1-7 5-10 11-10s10 3 11 10z" fill="#222"/></svg></div>
  <p class="card-body spaced abs">Torvel Capital's history in mergers and acquisitions traces back to 1998. We pride our selves in successfully</p>
  <a class="read-more abs">READ MORE »</a>
</section>

<section class="card abs" style="left:456px">
  <h2 class="card-title abs"><span class="mark"></span><span><em>What</em> We Do</span></h2>
  <div class="card-icon abs"><svg width="34" height="30" viewBox="0 0 34 30"><circle cx="12" cy="18" r="8" fill="none" stroke="#222" stroke-width="5" stroke-dasharray="4 2.3"/><circle cx="25" cy="8" r="5" fill="none" stroke="#222" stroke-width="3.5" stroke-dasharray="2.6 1.6"/></svg></div>
  <ul class="card-body services abs">
    <li>Buy-Side Acquisitions</li>
    <li>Recapitalizations &amp; Growth Capital Partnerships</li>
    <li>Sell-Side Transactions</li>
  </ul>
  <a class="read-more abs">READ MORE »</a>
</section>

<section class="card abs" style="left:778px">
  <h2 class="card-title abs"><span class="mark"></span><span><em>Latest</em> News</span></h2>
  <div class="card-icon abs"><svg width="32" height="28" viewBox="0 0 32 28"><path d="M3 9h8l14-7v24L11 19H3z" fill="#222"/><rect x="6" y="19" width="5" height="7" fill="#222"/></svg></div>
  <div class="card-body abs"><strong>Kauitm veleum iriure lorrfu</strong><br>Hdrehrit in vulptate velit essehi molestie coequa. molestie uitmi veleum iriure lorrfu hdrehrit</div>
  <a class="read-more abs">READ MORE »</a>
</section>

<div class="divider abs"></div>
<h2 class="testi-label abs"><em>Client</em><br>Testimonials</h2>
<svg class="testi-arrow abs" width="32" height="80" viewBox="0 0 32 80"><path d="M0 0L30 40L0 80Z" fill="rgba(255,255,255,.45)"/></svg>
<p class="testi-quote abs"><svg width="22" height="18" viewBox="0 0 22 18" style="vertical-align:-2px"><path d="M2 16V8q0-6 6-7v3q-3 1-3 4h3v8zM13 16V8q0-6 6-7v3q-3 1-3 4h3v8z" fill="#999"/></svg> Lorem ipsum sit amet consectet uradi incididunt ut labore et dolore magna aliquaps enimi ad minim veniam quiidunt ut labore etpvloore magn incididunt ut labore et dolore na aliquatmp enimt ad minim veniam quiidunt ut labore <svg width="22" height="18" viewBox="0 0 22 18" style="vertical-align:-8px"><path d="M20 2v8q0 6-6 7v-3q3-1 3-4h-3V2zM9 2v8q0 6-6 7v-3q3-1 3-4H3V2z" fill="#999"/></svg></p>
<p class="testi-name abs">Mr. Dolore na Aliqua</p>

<footer class="site-footer abs">
  <h3 class="foot-h abs" style="left:133px;top:23px">Contact Info</h3>
  <div class="foot-rule abs" style="left:133px;top:44px;width:366px"></div>
  <svg class="abs" style="left:134px;top:59px" width="11" height="15" viewBox="0 0 11 15"><path d="M5.5 0A5.5 5.5 0 0 0 0 5.5C0 9 5.5 15 5.5 15S11 9 11 5.5A5.5 5.5 0 0 0 5.5 0z" fill="#c9d6ea"/><circle cx="5.5" cy="5.5" r="2" fill="#1f4d8f"/></svg>
  <p class="address abs">Hong Kong: Room 1804<br>Harbourline Centre<br>27 - 35 Lockhart Road East<br>Wanchai, Hong Kong</p>
  <div class="foot-line abs" style="left:338px;top:55px"><svg width="10" height="16" viewBox="0 0 10 16"><rect x="1" y="0.5" width="8" height="15" rx="1.5" fill="none" stroke="#c9d6ea"/><rect x="2.5" y="2.5" width="5" height="8" fill="#c9d6ea"/></svg>469-555-0187</div>
  <div class="foot-line abs" style="left:337px;top:88px"><svg width="14" height="10" viewBox="0 0 14 10"><rect x="0.5" y="0.5" width="13" height="9" fill="none" stroke="#c9d6ea"/><path d="M0.5 0.5l6.5 5 6.5-5" fill="none" stroke="#c9d6ea"/></svg>info@torvelcapital.com</div>

  <h3 class="foot-h abs" style="left:554px;top:23px">Newsletter Signup</h3>
  <div class="foot-rule abs" style="left:554px;top:44px;width:240px"></div>
  <div class="news-input abs">Enter your email</div>
  <div class="news-go abs">GO</div>
  <div class="follow abs">Follow Us On:
    <span class="social" aria-label="Social profile one"></span>
    <span class="social" aria-label="Social profile two"></span>
    <span class="social" aria-label="Social profile three"></span>
    <span class="social" aria-label="Social profile four"></span>
  </div>

  <div class="foot-badge abs"><span></span></div>
  <p class="copyright abs">© Copyright 2014 Torvel Capital.<br>All Rights Reserved</p>
</footer>

</body>
</html>
```